Stylish new business card needed!

Hello everyone! I am in need of a new business card design for an alarm company here in Hurricane WV. I have all fonts, color codes and logos provided for you use! We are a young company and like the style of a clean sleek looking business card. Would like it double sided, one side holding the logo and the other with your design!
Target Market(s)
The people that are looking for the newest tech for home automation and security
Industry/Entity Type
Alarm services; Home automation
Contact Information for Business Card
Name of person; position (Sales; Installer); Phone Number (555.418.7260); Employee cell Number; Website (www.GuardedByVelk.example); Employee Email; Double sided
Look and feel
Each slider illustrates characteristics of the customer's brand and the style your logo design should communicate.

```html
<!DOCTYPE html>
<html lang="en">
<head>
<meta charset="utf-8">
<title>Guarded By Velk – Business Card</title>
<link rel="stylesheet" href="https://fonts.googleapis.com/css2?family=Arimo:wght@400;700&display=swap">
<style>
  :root {
    --backdrop: #232323;
    --card: #1f1f22;
    --orange: #f48d4b;
    --grey: #9a9a9a;
    --white: #ffffff;
  }
  * { box-sizing: border-box; margin: 0; padding: 0; }
  html, body {
    width: 1200px; height: 780px; overflow: hidden;
    background: var(--backdrop);
    font-family: "Arimo", Arial, sans-serif;
  }
  .canvas {
    width: 1200px; height: 780px;
    display: flex; flex-direction: column; align-items: center; justify-content: center;
    gap: 34px;
  }
  .card {
    position: relative;
    width: 600px; height: 343px;
    background: var(--card);
    border-radius: 18px;
    overflow: hidden;
    border-bottom: 3px solid var(--orange);
    box-shadow: 0 10px 24px rgba(0,0,0,.55);
  }

  /* Brand name placeholder */
  .brand { position: absolute; display: flex; flex-direction: column; align-items: center; }
  .brand__mark { display: flex; align-items: center; }
  .brand__dot { border-radius: 50%; background: var(--orange); flex: none; }
  .brand__name { color: var(--orange); font-weight: 700; white-space: nowrap; }
  .brand__tagline {
    color: var(--orange); font-weight: 700; text-transform: uppercase; letter-spacing: 1px; white-space: nowrap;
  }

  .card--front .brand { left: 0; right: 0; top: 128px; }
  .card--front .brand__mark { gap: 16px; }
  .card--front .brand__dot { width: 34px; height: 34px; }
  .card--front .brand__name { font-size: 46px; }
  .card--front .brand__tagline { font-size: 14px; margin-top: 18px; }

  .card--back .brand { left: 20px; width: 262px; top: 128px; }
  .card--back .brand__mark { gap: 10px; }
  .card--back .brand__dot { width: 20px; height: 20px; }
  .card--back .brand__name { font-size: 27px; }
  .card--back .brand__tagline { font-size: 9px; margin-top: 12px; letter-spacing: .5px; }

  .divider {
    position: absolute; left: 296px; top: 40px; width: 2px; height: 190px; background: var(--white);
  }
  .contact { position: absolute; left: 326px; top: 44px; }
  .contact__name { font-size: 27px; font-weight: 700; color: var(--orange); }
  .contact__name span { color: var(--grey); }
  .contact__role { font-size: 15px; font-weight: 700; color: var(--white); margin-top: 2px; }
  .contact__list { list-style: none; margin-top: 20px; }
  .contact__item {
    display: flex; align-items: center; gap: 9px;
    color: var(--white); font-size: 14px; line-height: 22px;
  }
  .contact__item svg { width: 13px; height: 13px; flex: none; }

  .bands { position: absolute; left: 0; top: 0; width: 600px; height: 343px; }
</style>
</head>
<body>
<main class="canvas">

  <section class="card card--front" aria-label="Card front">
    <div class="brand">
      <div class="brand__mark">
        <span class="brand__dot"></span>
        <span class="brand__name">Guarded By Velk</span>
      </div>
      <span class="brand__tagline">Automation and Security Services</span>
    </div>
  </section>

  <section class="card card--back" aria-label="Card back">
    <svg class="bands" viewBox="0 0 600 343" aria-hidden="true">
      <path d="M0 304 L318 258 Q336 255 356 258 L0 330 Z" fill="var(--orange)"/>
      <path d="M322 248 L600 196 L600 214 Q598 226 582 230 L362 258 Q350 258 340 254 Z" fill="var(--grey)"/>
    </svg>

    <div class="brand">
      <div class="brand__mark">
        <span class="brand__dot"></span>
        <span class="brand__name">Guarded By Velk</span>
      </div>
      <span class="brand__tagline">Automation and Security Services</span>
    </div>

    <div class="divider"></div>

    <div class="contact">
      <p class="contact__name">Marta <span>Kovalik</span></p>
      <p class="contact__role">Sales; Installer</p>
      <ul class="contact__list">
        <li class="contact__item">
          <svg viewBox="0 0 24 24" fill="var(--orange)"><path d="M6.6 10.8a15 15 0 0 0 6.6 6.6l2.2-2.2c.3-.3.7-.4 1-.2 1.1.4 2.3.6 3.6.6.6 0 1 .4 1 1V20c0 .6-.4 1-1 1A17 17 0 0 1 3 4c0-.6.4-1 1-1h3.5c.6 0 1 .4 1 1 0 1.3.2 2.5.6 3.6.1.3 0 .7-.2 1z"/></svg>
          555.418.7260
        </li>
        <li class="contact__item">
          <svg viewBox="0 0 24 24" fill="none" stroke="var(--white)" stroke-width="2"><rect x="6" y="2" width="12" height="20" rx="2"/></svg>
          555.418.3391
        </li>
        <li class="contact__item">
          <svg viewBox="0 0 24 24" fill="var(--orange)"><circle cx="12" cy="12" r="10"/></svg>
          www.GuardedByVelk.example
        </li>
        <li class="contact__item">
          <svg viewBox="0 0 24 24" fill="none" stroke="var(--orange)" stroke-width="2"><rect x="3" y="6" width="18" height="13" rx="1"/><path d="M3 7l9 7 9-7"/></svg>
          info@GuardedByVelk.example
        </li>
      </ul>
    </div>
  </section>

</main>
</body>
</html>
```